I need a business card designed using the logo provided either vertical or horizontal......Harbourline Property Group is an Australian based real estate company that caters for the upper end of the market so the design of the business card "must reflect" the companies image!!
Colour combinations are optional but "must be realistic" and must be able to be accurately useable CMYK colours.
Please consider that any colours used "must be able to be used" and be suitable in following designs for "pull out banner signs" and "real estate signs".
The colours and the font in the attached designs are for example and other combinations are encouraged.
Target Market(s)
The High End of the Australian real estate market
Industry/Entity Type
Business
Contact Information for Business Card
Logo - Business Name - Director + Licensed Real Estate Agent - Mobile Number (Cell Phone) - Business Number - Fax - Email Address - Web address
Requirements
Must have
- Designs and colours (CMYK) that can easily be interpreted by an Australian printer.
Nice to have
- Some alternative ideas on colour and font..........the ones provided are ok and have been provided as an example but I am looking for alternative ideas
Should not have
- Loud, overly bright colours. Designs that do not reflect the professional standards of the business.
- Designs that look good on a computer monitor but can not be re-created on a printing press.............this is most important when it comes to shading etc.

```html
<!DOCTYPE html>
<html lang="en">
<head>
<meta charset="utf-8">
<title>Harbourline Property Group – Business Card</title>
<link rel="stylesheet" href="https://fonts.googleapis.com/css2?family=Michroma&family=Open+Sans:wght@400;600&display=swap">
<style>
  :root {
    --navy: #0b2d4f;
    --sky: #3d7fc4;
    --paper: #f4f4f4;
    --ink: #3a3a3a;
    --ink-dark: #1c2430;
    --backdrop: #d9d9d9;
  }
  * { box-sizing: border-box; margin: 0; padding: 0; }
  html, body { width: 1200px; height: 1192px; overflow: hidden; }
  body {
    background: var(--backdrop);
    font-family: "Open Sans", sans-serif;
    display: flex;
    flex-direction: column;
    align-items: center;
    justify-content: center;
    gap: 70px;
  }
  .card {
    position: relative;
    width: 700px;
    height: 400px;
    background: var(--paper);
    overflow: hidden;
    box-shadow: 0 6px 18px rgba(0,0,0,0.15);
  }
  .card__wave { position: absolute; inset: 0; width: 100%; height: 100%; }
  .brand {
    position: absolute;
    display: flex;
    align-items: center;
    gap: 12px;
  }
  .brand__mark { width: 22px; height: 22px; background: var(--sky); flex: none; }
  .brand__name {
    font-family: "Open Sans", sans-serif;
    font-weight: 600;
    font-size: 22px;
    line-height: 1.15;
    color: var(--ink-dark);
    letter-spacing: 0.5px;
  }
  .card--front .brand { left: 360px; top: 150px; }
  .card--back .brand { left: 440px; top: 165px; }
  .card--back .brand__name { font-size: 17px; }

  .contact { position: absolute; left: 50px; top: 40px; }
  .contact__name {
    font-family: "Michroma", sans-serif;
    font-size: 19px;
    letter-spacing: 3px;
    color: var(--navy);
  }
  .contact__role {
    font-family: "Michroma", sans-serif;
    font-size: 11px;
    letter-spacing: 2px;
    color: var(--sky);
    margin-top: 8px;
  }
  .contact__company {
    font-family: "Michroma", sans-serif;
    font-size: 11px;
    letter-spacing: 2px;
    color: var(--sky);
    margin-top: 16px;
  }
  .contact__address { font-size: 14px; color: var(--ink); margin-top: 6px; }
  .contact__list { list-style: none; margin-top: 10px; }
  .contact__item {
    display: flex; align-items: center; gap: 10px;
    font-size: 15px; color: var(--ink); line-height: 24px;
  }
  .contact__icon { width: 14px; height: 14px; flex: none; }
</style>
</head>
<body>

  <section class="card card--back" aria-label="Card front with company name">
    <svg class="card__wave" viewBox="0 0 700 400" preserveAspectRatio="none" aria-hidden="true">
      <path d="M0,135 C110,300 420,380 700,392 L700,400 L0,400 Z" fill="var(--sky)"/>
      <path d="M0,148 C112,310 420,384 700,400 L0,400 Z" fill="var(--navy)"/>
    </svg>
    <div class="brand">
      <span class="brand__mark"></span>
      <span class="brand__name">Harbourline<br>Property Group</span>
    </div>
  </section>

  <section class="card card--front" aria-label="Card back with contact details">
    <svg class="card__wave" viewBox="0 0 700 400" preserveAspectRatio="none" aria-hidden="true">
      <path d="M0,225 C150,330 430,385 700,390 L700,400 L0,400 Z" fill="var(--sky)"/>
      <path d="M0,238 C152,340 430,390 700,400 L0,400 Z" fill="var(--navy)"/>
    </svg>

    <div class="contact">
      <h1 class="contact__name">MARCUS HALE</h1>
      <p class="contact__role">CEO</p>
      <p class="contact__company">Harbourline Property Group</p>
      <p class="contact__address">18 Wharf Terrace, Millers Point, Sydney.</p>
      <ul class="contact__list">
        <li class="contact__item">
          <svg class="contact__icon" viewBox="0 0 14 14" aria-hidden="true"><rect x="3" y="1" width="8" height="12" rx="1.5" fill="none" stroke="var(--sky)" stroke-width="1.5"/></svg>
          +61 412 508 274
        </li>
        <li class="contact__item">
          <svg class="contact__icon" viewBox="0 0 14 14" aria-hidden="true"><path d="M3,1 L5,1 L6,4 L4.5,5 C5.5,7 7,8.5 9,9.5 L10,8 L13,9 L13,11 C13,12 12,13 11,13 C6,13 1,8 1,3 C1,2 2,1 3,1 Z" fill="var(--sky)"/></svg>
          +61 2 9316 4820
        </li>
        <li class="contact__item">
          <svg class="contact__icon" viewBox="0 0 14 14" aria-hidden="true"><rect x="1" y="3" width="12" height="8" fill="none" stroke="var(--sky)" stroke-width="1.5"/><path d="M1,3 L7,8 L13,3" fill="none" stroke="var(--sky)" stroke-width="1.5"/></svg>
          marcus@harbourlineproperty.com
        </li>
        <li class="contact__item">
          <svg class="contact__icon" viewBox="0 0 14 14" aria-hidden="true"><circle cx="7" cy="7" r="6" fill="none" stroke="var(--sky)" stroke-width="1.5"/><path d="M1,7 L13,7 M7,1 C4,4 4,10 7,13 M7,1 C10,4 10,10 7,13" fill="none" stroke="var(--sky)" stroke-width="1.2"/></svg>
          www.harbourlineproperty.com
        </li>
      </ul>
    </div>

    <div class="brand">
      <span class="brand__mark"></span>
      <span class="brand__name">Harbourline<br>Property Group</span>
    </div>
  </section>

</body>
</html>
```